Business card design needed

My business is in Matchmaking. My objective is to find the most compatible partner for my clients....basically I'm in the love and happiness industry bringing two people together for a lasting loving relationship.

I envision the design to be something with 2 people who are in love looking happy or even a silhouette.....I don't really know, I'm open to ideas.....maybe no picture at all, but I want it to be classy :-)

I do have a logo which I will upload. You can also go to my website to give you an idea on the colours and the design if that helps, however the website is not finished yet, it should be up by today or tomorrow. If the website has a heart with swirls on the upper left hand corner, that is the old website, please ignore that one. The one that will be up shortly has a picture frame on the home page with my logo that will be in the file I will upload on this page.

Target Market(s)

There are three categories: Over 45, Asian and Western and same sex, but would be able to afford to hire a matchmaker

Contact Information for Business Card

The Tidewell Bureau
Helping You Find The "One"
Mavis Ellery
Matchmaker
0492 517 264
info@tidewellbureau.com.au
www.tidewellbureau.com.au

```html
<!DOCTYPE html>
<html lang="en">
<head>
<meta charset="utf-8">
<title>The Tidewell Bureau – Business Card</title>
<link rel="stylesheet" href="https://fonts.googleapis.com/css2?family=Open+Sans:wght@400;600;700&display=swap">
<style>
  :root {
    --page-bg: #e4e8e8;
    --cream: #fbf8e6;
    --plum: #6e4a66;
    --plum-dark: #5e3d57;
    --teal: #6fb3a8;
    --white: #ffffff;
    --photo-light: #8a8a8a;
    --photo-dark: #1e1e1e;
  }
  * { margin: 0; padding: 0; box-sizing: border-box; }
  html, body {
    width: 1200px;
    height: 1000px;
    overflow: hidden;
    background: var(--page-bg);
    font-family: "Open Sans", Arial, sans-serif;
  }
  .canvas {
    position: relative;
    width: 1200px;
    height: 1000px;
  }
  .business-card {
    position: absolute;
    left: 180px;
    top: 260px;
    width: 840px;
    height: 480px;
    display: flex;
    box-shadow: 0 14px 30px rgba(0, 0, 0, 0.22);
    overflow: hidden;
  }
  .card-photo {
    width: 330px;
    height: 100%;
    background: radial-gradient(ellipse at 45% 55%, var(--photo-light) 0%, #4a4a4a 45%, var(--photo-dark) 100%);
  }
  .card-divider {
    width: 5px;
    height: 100%;
    background: var(--teal);
  }
  .card-info {
    flex: 1;
    display: flex;
    flex-direction: column;
  }
  .brand-panel {
    height: 262px;
    background: var(--cream);
    display: flex;
    flex-direction: column;
    align-items: center;
    justify-content: flex-end;
    padding-bottom: 26px;
  }
  .brand-mark {
    width: 64px;
    height: 64px;
    border-radius: 50%;
    background: var(--teal);
    margin-bottom: 22px;
  }
  .brand-name {
    font-size: 40px;
    font-weight: 600;
    color: var(--plum);
    letter-spacing: 0.5px;
    line-height: 1.1;
  }
  .brand-tagline {
    margin-top: 10px;
    font-size: 27px;
    font-weight: 700;
    color: var(--plum);
    letter-spacing: -0.3px;
  }
  .contact-panel {
    flex: 1;
    background: var(--plum);
    color: var(--white);
    padding: 20px 0 0 52px;
  }
  .contact-name {
    font-size: 34px;
    font-weight: 700;
    line-height: 1.15;
  }
  .contact-role {
    font-size: 22px;
    font-weight: 600;
    margin-top: 2px;
    margin-bottom: 26px;
  }
  .contact-line {
    font-size: 24px;
    font-weight: 600;
    line-height: 1.25;
  }
</style>
</head>
<body>
<main class="canvas">
  <section class="business-card">
    <div class="card-photo" role="img" aria-label="Black and white photograph of two clasped hands, one wearing an engagement ring"></div>
    <div class="card-divider"></div>
    <div class="card-info">
      <header class="brand-panel">
        <span class="brand-mark" aria-hidden="true"></span>
        <h1 class="brand-name">The Tidewell Bureau</h1>
        <p class="brand-tagline">Helping You Find The "One"</p>
      </header>
      <div class="contact-panel">
        <h2 class="contact-name">Mavis Ellery</h2>
        <p class="contact-role">Matchmaker</p>
        <p class="contact-line">Tel. 0492 517 264</p>
        <p class="contact-line">mavis@tidewellbureau.com.au</p>
        <p class="contact-line">www.tidewellbureau.com.au</p>
      </div>
    </div>
  </section>
</main>
</body>
</html>
```